New Business Card Design for Manufacturing

We are an engineering/manufacturing company that offers Advanced machining/assembly/engineering services, as well as innovative products for the heavy duty engine cooling markets.

We are looking to get a new business card designed that is clean and modern looking, but still fits the wide range of technical/skilled work we do.

- We hope to use this design as the base for other design work in new Presentations, web, and print work.

Industry/Entity Type

Engineering

Contact Information for Business Card

Our preferred color of blue is (RGB) 22/71/159 but can vary slightly from that color. Our content will be our Logo and full company name (Vantrell Forge Works, Inc.), company address, name, job title, phone number with extension, cell number, fax number, website, and email address on the cards.
We'd like the full company name next to the logo, but we are open to other interpretations of that layout.
Preferably, we would like the back side to be clean with just our logo, and the front to contain all of the contact information.

Colors
2f74b4
0355a3
85abd2

Requirements
Must have
• - Logo, company name, needed content - We are open to interpretation beyond that.
• - Standard size business card.
• - Horizontal orientation.
• - Enough space for lengthy names / job titles (for example, a job title could read "Directory of Human Resources" or "V.P. of Governmental Affairs"). We need this to look clean, whether the title be short (CEO) or long (as described above).

```html
<!DOCTYPE html>
<html lang="en">
<head>
<meta charset="utf-8">
<title>Vantrell Forge Works — Business Card</title>
<link rel="stylesheet" href="https://fonts.googleapis.com/css2?family=Roboto:wght@400;700;900&family=Roboto+Condensed:wght@500&display=swap">
<style>
  :root {
    --backdrop: #2b2b2b;
    --brand-blue: #0f50a0;
    --card-white: #f2f2f2;
    --slate-grey: #7b7f83;
    --ink-white: #ffffff;
  }
  * { box-sizing: border-box; margin: 0; padding: 0; }
  html, body {
    width: 1200px; height: 960px; overflow: hidden;
    background: var(--backdrop);
    font-family: "Roboto", Arial, sans-serif;
  }
  .stage { position: relative; width: 1200px; height: 960px; }
  .card {
    position: absolute; width: 600px; height: 343px; overflow: hidden;
  }
  .card-front { left: 314px; top: 113px; background: var(--card-white); }
  .card-back { left: 311px; top: 472px; background: var(--brand-blue); }

  .card-shapes { position: absolute; inset: 0; }

  .wordmark {
    position: absolute; display: flex; align-items: center; gap: 12px;
    font-family: "Roboto", Arial, sans-serif; font-weight: 900;
    text-transform: uppercase; line-height: 1;
  }
  .wordmark-square { width: 18px; height: 18px; flex: none; }
  .card-front .wordmark {
    left: 58px; top: 140px; color: var(--brand-blue); font-size: 27px;
  }
  .card-front .wordmark-square { background: var(--brand-blue); }
  .wordmark-name { display: block; }

  .card-back .wordmark {
    left: 0; right: 0; top: 158px; justify-content: center;
    color: var(--ink-white); font-size: 28px;
  }
  .card-back .wordmark-square { background: var(--ink-white); }

  .contact-panel {
    position: absolute; left: 359px; top: 84px; color: var(--ink-white);
  }
  .person-name {
    font-family: "Roboto Condensed", "Arial Narrow", sans-serif;
    font-weight: 500; font-size: 23px; line-height: 1; letter-spacing: 0.2px;
  }
  .person-title { font-size: 14.5px; line-height: 1.2; margin-top: 3px; }
  .address { font-size: 14.5px; line-height: 18px; margin-top: 7px; }
  .contact-list { list-style: none; margin-top: 9px; }
  .contact-list li {
    display: flex; align-items: center; gap: 8px;
    font-size: 14.5px; line-height: 19.5px;
  }
  .contact-icon { width: 13px; height: 13px; flex: none; fill: var(--ink-white); }
</style>
</head>
<body>
<main class="stage">

  <section class="card card-front" aria-label="Business card front">
    <svg class="card-shapes" width="600" height="343" viewBox="0 0 600 343" aria-hidden="true">
      <polygon class="accent-strip" points="0,61 30,61 0,282" fill="var(--slate-grey)"/>
      <polygon class="contact-band" points="334,61 600,61 600,281 305,281" fill="var(--brand-blue)"/>
    </svg>

    <div class="wordmark">
      <span class="wordmark-square"></span>
      <span class="wordmark-name">Vantrell<br>Forge Works</span>
    </div>

    <div class="contact-panel">
      <p class="person-name">DORIAN VALE</p>
      <p class="person-title">V.P. of Governmental Affairs</p>
      <p class="address">4120 Alder Ridge Road<br>Kenai, Alaska 99611</p>
      <ul class="contact-list">
        <li>
          <svg class="contact-icon" viewBox="0 0 16 16" aria-label="Phone"><path d="M3.2 1.2l2.4-.4 1.6 3.6-1.6 1.2c.9 2 2.4 3.5 4.4 4.4l1.2-1.6 3.6 1.6-.4 2.4c-.2.8-1 1.4-1.8 1.3C6.8 13.1 2.9 9.2 1.9 3c-.1-.8.5-1.6 1.3-1.8z"/></svg>
          <span>555 214 7730</span>
        </li>
        <li>
          <svg class="contact-icon" viewBox="0 0 16 16" aria-label="Mobile"><path d="M4.5 0h7A1.5 1.5 0 0 1 13 1.5v13a1.5 1.5 0 0 1-1.5 1.5h-7A1.5 1.5 0 0 1 3 14.5v-13A1.5 1.5 0 0 1 4.5 0zM5 2v10h6V2zm3 11a1 1 0 1 0 0 2 1 1 0 0 0 0-2z"/></svg>
          <span>555 306 1189</span>
        </li>
        <li>
          <svg class="contact-icon" viewBox="0 0 16 16" aria-label="Email"><path d="M1 4h14v9H1zM2 5.2v.4l6 3.8 6-3.8v-.4z"/></svg>
          <span>dorian@vantrellforge.com</span>
        </li>
        <li>
          <svg class="contact-icon" viewBox="0 0 16 16" aria-label="Website"><circle cx="8" cy="8" r="7"/><path d="M4 5c1 0 2 1 2 2s1 1 1 2-1 2 0 3M10 2.5c0 1 1 1.5 2 1.5M11 9c1 0 1.5 1 1 2" stroke="var(--brand-blue)" stroke-width="1.3" fill="none"/></svg>
          <span>www.vantrellforge.com</span>
        </li>
      </ul>
    </div>
  </section>

  <section class="card card-back" aria-label="Business card back">
    <div class="wordmark">
      <span class="wordmark-square"></span>
      <span class="wordmark-name">Vantrell Forge Works, Inc.</span>
    </div>
  </section>

</main>
</body>
</html>
```